Naturopath Practitioner Card Design

I am a naturopath needing a design for a business card mainly to show that I am a naturopath and have some contact details to give to prospective clients. I am open minded about the design and what is on the second side of the card whether it just be some artwork or space for details, appointment times etc. Naturopathy is the practice of natural medicine that uses a holistic approach and incorporates herbal and nutritional medicine.

Industry/Entity Type

Business

Contact Information for Business Card

Tom Rudd NaturopathBHSc (Naturopathy) Member WHPG 0487 925 316 tom.rudd@mailexample.com www.tomruddnaturopathy.example.au

Requirements
Nice to have
• Would prefer some kind of original pattern/art work/logo rather than an image, not fussed if its very simple/basic
• I am open to any colour but think I would prefer a more earthy sandy clay etc type style than the greens that are commonly associated with naturopathy.
Should not have
• Don't really want to have generic stock images on it

```html
<!DOCTYPE html>
<html lang="en">
<head>
<meta charset="utf-8">
<title>Tom Rudd Naturopath – Business Card</title>
<link rel="stylesheet" href="https://fonts.googleapis.com/css2?family=Open+Sans:ital,wght@0,400;0,600;0,700;1,700&display=swap">
<style>
  :root {
    --leaf-green: #5a9e3a;
    --band-green: #5fa33f;
    --soft-green: #cfe6b0;
    --pale-green: #eef6e2;
    --ink: #333333;
    --card-white: #ffffff;
    --page-bg: #e9e7e2;
  }
  * { box-sizing: border-box; margin: 0; padding: 0; }
  html, body {
    width: 1200px; height: 900px; overflow: hidden;
    background: var(--page-bg);
    font-family: "Open Sans", Arial, sans-serif;
    color: var(--ink);
  }
  .card {
    position: absolute;
    left: 240px;
    width: 720px; height: 410px;
    background: var(--card-white);
    overflow: hidden;
    box-shadow: 0 4px 14px rgba(0,0,0,0.15);
  }
  .card--front { top: 30px; }
  .card--back { top: 462px; }

  /* Front side */
  .front-backdrop {
    position: absolute; inset: 0;
    background:
      radial-gradient(ellipse 60% 70% at 62% 40%, var(--soft-green) 0%, var(--pale-green) 45%, rgba(255,255,255,0) 80%),
      linear-gradient(90deg, #ffffff 0%, #ffffff 30%, #f1f8e8 60%, #e3f0d2 100%);
  }
  .foliage {
    position: absolute;
  }
  .foliage--top-left {
    left: -20px; top: -20px; width: 270px; height: 140px;
    border-radius: 0 0 60% 10%;
    background: radial-gradient(ellipse at 45% 40%, #4f9a2c 0%, #7dbb4e 40%, rgba(170,215,130,0.5) 70%, rgba(255,255,255,0) 100%);
  }
  .foliage--right {
    left: 420px; top: 70px; width: 320px; height: 350px;
    border-radius: 50% 0 0 40%;
    background: radial-gradient(ellipse at 65% 55%, #3f8f25 0%, #6cb244 35%, rgba(150,205,110,0.6) 65%, rgba(255,255,255,0) 100%);
  }
  .contact {
    position: absolute; left: 42px; top: 128px;
  }
  .contact__name {
    font-size: 25px; font-weight: 700; color: var(--leaf-green); line-height: 1.1;
  }
  .contact__title, .contact__credentials {
    font-size: 17px; line-height: 1.3;
  }
  .contact__list { list-style: none; margin-top: 14px; }
  .contact__item {
    display: flex; align-items: center; gap: 10px;
    font-size: 17px; line-height: 1.45;
  }
  .contact__icon { width: 14px; height: 14px; flex: none; }
  .green-bands {
    position: absolute; left: 0; bottom: 0; width: 720px; height: 80px;
  }

  /* Back side */
  .appointment__heading {
    position: absolute; left: 300px; top: 44px;
    font-size: 27px; font-weight: 700; color: var(--leaf-green);
  }
  .appointment__label {
    position: absolute; left: 44px; font-size: 16px;
  }
  .appointment__line {
    position: absolute; height: 1px; background: var(--ink);
  }
  .appointment__meridiem {
    position: absolute; font-size: 16px;
  }
  .appointment__notice {
    position: absolute; left: 44px; top: 320px; width: 640px;
    font-size: 17px; font-weight: 700; font-style: italic; color: var(--leaf-green);
  }
</style>
</head>
<body>

<section class="card card--front" aria-label="Business card front">
  <div class="front-backdrop" role="img" aria-label="Soft blurred green foliage background"></div>
  <div class="foliage foliage--top-left" role="img" aria-label="Fresh green leaves on a branch"></div>
  <div class="foliage foliage--right" role="img" aria-label="Green leafy branches"></div>

  <div class="contact">
    <h1 class="contact__name">Tom Rudd</h1>
    <p class="contact__title">Naturopath</p>
    <p class="contact__credentials">BHSc (Naturopathy) Member WHPG</p>
    <ul class="contact__list">
      <li class="contact__item">
        <svg class="contact__icon" viewBox="0 0 24 24" aria-hidden="true"><path fill="#5a9e3a" d="M6.6 10.8a15.2 15.2 0 0 0 6.6 6.6l2.2-2.2c.3-.3.7-.4 1-.2 1.1.4 2.3.6 3.6.6.6 0 1 .4 1 1V20c0 .6-.4 1-1 1A17 17 0 0 1 3 4c0-.6.4-1 1-1h3.5c.6 0 1 .4 1 1 0 1.3.2 2.5.6 3.6.1.3 0 .7-.2 1z"/></svg>
        <span>0487 925 316</span>
      </li>
      <li class="contact__item">
        <svg class="contact__icon" viewBox="0 0 24 24" aria-hidden="true"><rect x="2" y="5" width="20" height="14" rx="1.5" fill="#5a9e3a"/><path d="M3 6l9 7 9-7" fill="none" stroke="#fff" stroke-width="1.6"/></svg>
        <span>tom.rudd@mailexample.com</span>
      </li>
    </ul>
  </div>

  <svg class="green-bands" viewBox="0 0 720 80" aria-hidden="true">
    <polygon points="0,4 292,4 280,20 0,20" fill="#5fa33f"/>
    <polygon points="300,20 312,8 720,8 720,80 300,80" fill="#5fa33f"/>
  </svg>
</section>

<section class="card card--back" aria-label="Business card back">
  <h2 class="appointment__heading">Your Next Appointment is</h2>

  <span class="appointment__label" style="top:100px">Name :</span>
  <div class="appointment__line" style="left:130px; top:120px; width:550px"></div>

  <span class="appointment__label" style="top:150px">Date :</span>
  <div class="appointment__line" style="left:130px; top:170px; width:550px"></div>

  <span class="appointment__label" style="top:200px">Time:</span>
  <div class="appointment__line" style="left:130px; top:220px; width:250px"></div>
  <span class="appointment__meridiem" style="left:392px; top:206px">AM</span>
  <div class="appointment__line" style="left:440px; top:270px; width:220px"></div>
  <span class="appointment__meridiem" style="left:672px; top:256px">PM</span>

  <p class="appointment__notice">If unable to keep appointment, kindly give 24hrs notice.</p>
</section>

</body>
</html>
```